A5 Magazine Cover Design

I need a front cover designing for a new community magazine called ORLEEN. ORLEEN will be listing local buisnesses and local interest articles for the residents in my area. I need the look to be clean but inviting.

I will consider any colour combination as long as its not too bright.

```html
<!DOCTYPE html>
<html lang="en">
<head>
<meta charset="utf-8">
<title>Orleen — Magazine Cover</title>
<link rel="stylesheet" href="https://fonts.googleapis.com/css2?family=Inter:wght@600;800&display=swap">
<style>
  :root {
    --stage: #1b1b1b;
    --paper: #f7f7f7;
    --smoke-light: #eceeee;
    --smoke-mid: #c9cfcf;
    --smoke-dark: #8f9a9b;
    --panel: rgba(150, 150, 150, 0.28);
    --title: #2a2730;
    --tagline: #ffffff;
    --rule: #ffffff;
    --dot-rose: #d9778f;
    --dot-plum: #b87ab8;
    --dot-sky: #79a8cf;
    --dot-teal: #79c9b8;
    --dot-mint: #84cf98;
    --dot-lime: #c3dc84;
    --dot-sand: #dfd08c;
    --dot-apricot: #e3b48c;
    --wave-a: #e8d9dc;
    --wave-b: #cfc6c4;
  }

  * { margin: 0; padding: 0; box-sizing: border-box; }

  html, body {
    width: 1200px;
    height: 1030px;
    overflow: hidden;
    background: var(--stage);
  }

  .canvas {
    position: relative;
    width: 1200px;
    height: 1030px;
  }

  .cover {
    position: absolute;
    left: 262px;
    top: 35px;
    width: 675px;
    height: 960px;
    background: var(--paper);
    overflow: hidden;
    font-family: "Inter", Arial, sans-serif;
  }

  .cover__smoke {
    position: absolute;
    inset: 0;
    background:
      radial-gradient(ellipse 70% 18% at 55% 26%, var(--smoke-dark) 0%, transparent 70%),
      radial-gradient(ellipse 80% 25% at 40% 45%, var(--smoke-mid) 0%, transparent 75%),
      linear-gradient(180deg, var(--paper) 0%, var(--smoke-light) 40%, var(--paper) 80%);
    opacity: 0.9;
  }

  .cover__panel {
    position: absolute;
    left: 35px;
    top: 262px;
    width: 603px;
    height: 519px;
    background: var(--panel);
  }

  .masthead {
    position: absolute;
    left: 48px;
    top: 62px;
    font-size: 150px;
    font-weight: 800;
    letter-spacing: -7px;
    line-height: 1;
    color: var(--title);
  }

  .tagline {
    position: absolute;
    left: 51px;
    top: 280px;
    font-size: 62px;
    font-weight: 600;
    letter-spacing: -1.5px;
    line-height: 60px;
    color: var(--tagline);
  }

  .rules {
    position: absolute;
    left: 51px;
    top: 543px;
    width: 457px;
  }

  .rules__line {
    display: block;
    background: var(--rule);
    margin-bottom: 6px;
  }
  .rules__line--thick { height: 10px; }
  .rules__line--thin { height: 4px; }

  .dots {
    position: absolute;
    left: 52px;
    top: 652px;
    display: flex;
    gap: 9px;
  }

  .dots__dot {
    width: 64px;
    height: 64px;
    border-radius: 50%;
    opacity: 0.85;
  }
  .dots__dot--rose { background: var(--dot-rose); }
  .dots__dot--plum { background: var(--dot-plum); }
  .dots__dot--sky { background: var(--dot-sky); }
  .dots__dot--teal { background: var(--dot-teal); }
  .dots__dot--mint { background: var(--dot-mint); }
  .dots__dot--lime { background: var(--dot-lime); }
  .dots__dot--sand { background: var(--dot-sand); }
  .dots__dot--apricot { background: var(--dot-apricot); }

  .cover__waves {
    position: absolute;
    left: 0;
    bottom: 0;
    width: 675px;
    height: 200px;
    background:
      radial-gradient(ellipse 30% 45% at 45% 75%, var(--wave-a) 0%, transparent 80%),
      linear-gradient(180deg, transparent 0%, var(--wave-b) 60%, var(--wave-a) 100%);
  }
</style>
</head>
<body>
  <main class="canvas">
    <article class="cover">
      <div class="cover__smoke" role="img" aria-label="Soft grey smoke texture across the cover"></div>
      <div class="cover__panel"></div>

      <h1 class="masthead">Orleen</h1>

      <p class="tagline">Searches<br>Reviews and<br>Recommends<br>Locally</p>

      <div class="rules" aria-hidden="true">
        <span class="rules__line rules__line--thick"></span>
        <span class="rules__line rules__line--thin"></span>
        <span class="rules__line rules__line--thin"></span>
      </div>

      <div class="dots" aria-hidden="true">
        <span class="dots__dot dots__dot--rose"></span>
        <span class="dots__dot dots__dot--plum"></span>
        <span class="dots__dot dots__dot--sky"></span>
        <span class="dots__dot dots__dot--teal"></span>
        <span class="dots__dot dots__dot--mint"></span>
        <span class="dots__dot dots__dot--lime"></span>
        <span class="dots__dot dots__dot--sand"></span>
        <span class="dots__dot dots__dot--apricot"></span>
      </div>

      <div class="cover__waves" role="img" aria-label="Decorative flowing line waves with scattered bubbles"></div>
    </article>
  </main>
</body>
</html>
```